Construction Company Cellar Crafters needs Business Card

I would like modern looking business card design. I am attaching logo of our company. Please include cell nr 302.418.7650 , email address cellarcrafters4u@examplemail.com, web : cellarcrafters4u.com, please also include wording: Specializing in finishing and remodeling basements. You can play with dark grey and orange colors or any ideas are welcome. Also include social media icons Friendloop and HouseGuidr.

```html
<!DOCTYPE html>
<html lang="en">
<head>
<meta charset="utf-8">
<title>Cellar Crafters – Business Card</title>
<link rel="stylesheet" href="https://fonts.googleapis.com/css2?family=Orbitron:wght@500&family=Open+Sans:wght@400;600&display=swap">
<style>
  :root {
    --stage: #ebe6e1;
    --card-black: #000000;
    --brand-orange: #f05a28;
    --band-grey: #c8c8c8;
    --text-white: #ffffff;
    --badge-green: #6cbf3f;
  }
  * { margin: 0; padding: 0; box-sizing: border-box; }
  html, body { width: 1200px; height: 900px; overflow: hidden; }
  body { background: var(--stage); position: relative; font-family: "Open Sans", Arial, sans-serif; }

  .card { position: absolute; overflow: hidden; background: var(--card-black); }
  .card--front { left: 78px; top: 35px; width: 587px; height: 362px; }
  .card--back  { left: 388px; top: 505px; width: 567px; height: 352px; }

  .front-shape { position: absolute; left: 0; top: 0; }

  .brand-name {
    position: absolute;
    font-family: "Orbitron", "Arial Black", sans-serif;
    font-weight: 500;
    color: var(--brand-orange);
    letter-spacing: 2px;
    white-space: nowrap;
    display: flex; align-items: center; gap: 14px;
  }
  .brand-mark { width: 26px; height: 26px; background: var(--brand-orange); display: inline-block; }
  .card--front .brand-name { left: 0; width: 587px; justify-content: center; top: 108px; font-size: 34px; }
  .card--back .brand-name { left: 0; width: 567px; justify-content: center; top: 160px; font-size: 34px; }

  .contact-list { position: absolute; left: 30px; top: 256px; list-style: none; }
  .contact-list li {
    display: flex; align-items: center; gap: 8px;
    color: var(--text-white); font-size: 17px; line-height: 24.5px;
  }
  .contact-icon { width: 12px; height: 12px; flex: none; }

  .social-row {
    position: absolute; right: 36px; top: 271px;
    display: flex; align-items: center; gap: 14px;
  }
  .social-name { color: var(--text-white); font-size: 13px; font-weight: 600; }
  .listing-badge { width: 40px; height: 40px; background: var(--badge-green); border-radius: 4px; }

  .tagline {
    position: absolute; left: 0; width: 567px; top: 262px;
    text-align: center;
    font-family: "Orbitron", "Arial Black", sans-serif; font-weight: 500;
    color: var(--brand-orange); font-size: 16px; line-height: 27px; letter-spacing: 1.2px;
    text-transform: uppercase;
  }
</style>
</head>
<body>

<section class="card card--front" aria-label="Business card front">
  <svg class="front-shape" width="587" height="362" viewBox="0 0 587 362" aria-hidden="true">
    <polygon points="0,198 392,198 410,191 0,191" fill="var(--card-black)"/>
    <polygon points="0,198 400,198 382,223 0,223" fill="var(--band-grey)"/>
    <polygon points="0,226 382,226 412,191 587,191 587,362 0,362" fill="var(--brand-orange)"/>
    <polyline points="0,225 381,225 411,190 587,190" fill="none" stroke="#111" stroke-width="2"/>
  </svg>

  <div class="brand-name"><span class="brand-mark"></span>CELLAR CRAFTERS</div>

  <ul class="contact-list">
    <li>
      <svg class="contact-icon" viewBox="0 0 12 12" aria-hidden="true"><rect x="3" y="0.5" width="6" height="11" rx="1" fill="none" stroke="#fff" stroke-width="1.2"/><circle cx="6" cy="9.5" r="0.7" fill="#fff"/></svg>
      302.418.7650
    </li>
    <li>
      <svg class="contact-icon" viewBox="0 0 12 12" aria-hidden="true"><rect x="0.5" y="2.5" width="11" height="7.5" fill="#fff"/><polyline points="0.5,2.5 6,7 11.5,2.5" fill="none" stroke="#f05a28" stroke-width="1"/></svg>
      cellarcrafters4u@examplemail.com
    </li>
    <li>
      <svg class="contact-icon" viewBox="0 0 12 12" aria-hidden="true"><circle cx="6" cy="6" r="5.5" fill="#fff"/><path d="M6 0.5 C3 3 3 9 6 11.5 M6 0.5 C9 3 9 9 6 11.5 M0.5 6 H11.5" fill="none" stroke="#f05a28" stroke-width="0.8"/></svg>
      cellarcrafters4u.com
    </li>
  </ul>

  <div class="social-row">
    <span class="social-name">Friendloop</span>
    <span class="social-name">HouseGuidr</span>
    <span class="listing-badge" aria-label="Listing badge"></span>
  </div>
</section>

<section class="card card--back" aria-label="Business card back">
  <div class="brand-name"><span class="brand-mark"></span>CELLAR CRAFTERS</div>
  <p class="tagline">Specializing in finishing and<br>remodeling basements.</p>
</section>

</body>
</html>
```